Business card design and logo needed - Photographer

I take photos of weddings, rodeos, snowmobiling.
Need a card to hand out to prospective clients.
Industry/Entity Type
Business
Contact Information for Business Card
Marcus Tollen Photography
Requirements
Must have
- Bold
Black or white base.
My website. www.MarcusTollen-example.com
Should not have
- camera/ lens/ aperture blades

```html
<!DOCTYPE html>
<html lang="en">
<head>
<meta charset="utf-8">
<title>Marcus Tollen Photography — Business Card</title>
<link href="https://fonts.googleapis.com/css2?family=Bebas+Neue&family=Teko:wght@500&display=swap" rel="stylesheet">
<style>
  :root {
    --paper: #ffffff;
    --card: #000000;
    --ink: #ffffff;
  }
  html, body {
    margin: 0;
    padding: 0;
    width: 1200px;
    height: 693px;
    overflow: hidden;
    background: var(--paper);
  }
  .canvas {
    position: relative;
    width: 1200px;
    height: 693px;
    background: var(--paper);
  }
  .card {
    position: absolute;
    left: 29px;
    top: 29px;
    width: 1158px;
    height: 644px;
    background: var(--card);
    color: var(--ink);
  }
  .brand-mark {
    position: absolute;
    left: 579px;
    top: 257px;
    width: 0;
    height: 0;
  }
  .brand-mark__ring {
    position: absolute;
    left: -120px;
    top: -120px;
    width: 240px;
    height: 240px;
    display: flex;
    align-items: center;
    justify-content: center;
  }
  .brand-mark__ring svg {
    position: absolute;
    inset: 0;
  }
  .brand-mark__name {
    position: relative;
    font-family: "Teko", sans-serif;
    font-weight: 500;
    font-size: 64px;
    line-height: 1;
    letter-spacing: 0.04em;
    color: var(--ink);
    padding-top: 8px;
  }
  .card__details {
    position: absolute;
    left: 0;
    right: 0;
    top: 444px;
    text-align: center;
  }
  .card__title {
    margin: 0;
    font-family: "Bebas Neue", sans-serif;
    font-weight: 400;
    font-size: 54px;
    line-height: 1;
    letter-spacing: 0.005em;
    color: var(--ink);
  }
  .card__contact {
    margin: 10px 0 0;
    font-family: "Teko", sans-serif;
    font-weight: 500;
    font-size: 14px;
    line-height: 1.7;
    letter-spacing: 0.55em;
    color: var(--ink);
  }
  .card__contact span {
    display: block;
    padding-left: 0.55em;
  }
</style>
</head>
<body>
  <div class="canvas">
    <section class="card">
      <div class="brand-mark">
        <div class="brand-mark__ring">
          <svg width="240" height="240" viewBox="0 0 240 240" aria-hidden="true">
            <circle cx="120" cy="120" r="112" fill="none" stroke="#ffffff" stroke-width="6"/>
          </svg>
          <span class="brand-mark__name">MT</span>
        </div>
      </div>

      <div class="card__details">
        <h1 class="card__title">MARCUS TOLLEN PHOTOGRAPHY</h1>
        <p class="card__contact">
          <span class="card__phone">(306) 555 0142</span>
          <span class="card__web">WWW.MARCUSTOLLEN-EXAMPLE.COM</span>
        </p>
      </div>
    </section>
  </div>
</body>
</html>
```